Online Games Mobile Website Design

Important information:<br/>Style:<br/>- minimalistic flat<br/>- attention to the elements<br/>- The background is everywhere white, except for header, menu and footer.<br/>- everything is flat, without shadows, roundings, bulges, gradients<br/>- free choice of colors<br/>- use bright colors for contrasts<br/>- for a specific page, it is important to save every pixel in height (no need to make pointlessly large indents where they are not needed)<br/><br/>Fonts (recommended, but not required):<br/>for titles (red in layout) - Google sans<br/>for the rest of the text - Roboto<br/><br/>Features:<br/>All pictures of games (pictures with previews of games) should be with an aspect ratio of 16: 9, no others, this should immediately be taken into account.<br/><br/>Additionally, you need to make a logo redesign that will suit the new design.<br/><br/><br/>Specifically about the page to be redesigned - Page of the game<br/>This page contains the game and a list of similar games.<br/><br/>Check attached image for the layout details.<br/><br/>The description of the game is shown by clicking on the name of the game under the game.<br/>For evaluation, you need to provide a page with an open / hidden description of the game.<br/>When the description of the game is disclosed, there are Tag 1, Tag 2, Tag 3 labels - these are the tags to which the game belongs (shooter, arcade, racing, etc.).<br/>You need to choose a set of icons for tags, then use them on these labels.<br/><br/>Under the game (portrait) is a list of similar games.<br/>You must provide 3 options for this list:<br/><br/>1. List items have a border and are separated by indentation.<br/>2. List items without a border are separated by a horizontal line.<br/>3. Items without a border are only separated by indentation<br/>for point 2 and 3, center the text (to the right of the game image) along the upper left edge, as in a relayed video on youtube<br/><br/>For the design layout use pictures, texts, game names from the website Vultaroo.com.

Hello, I've posted my project just today. Thanks in advance

Target Market(s)

Mobile online games

Logo Text

Vultaroo / Online games

Number of Pages Required

1 page

Font styles to use
Sans Serif

Colors

Designer to choose colors to be used in the design.

Requirements
Must have
• Check our current Game Page view and do something that really much much better - https://vultaroo.com/winter-otter-dash-177/

```html
<!DOCTYPE html>
<html lang="en">
<head>
<meta charset="utf-8">
<title>Vultaroo – Winter Otter Dash</title>
<link href="https://fonts.googleapis.com/css2?family=Roboto:wght@400;500;700;900&display=swap" rel="stylesheet">
<style>
  :root{
    --canvas:#6a6d6e;
    --content:#ffffff;
    --header:#1c3127;
    --card-line:#d5ddd8;
    --brand:#3cc35f;
    --red:#e3231b;
    --ink:#1c2a23;
    --muted:#5f6b65;
    --light:#ffffff;
  }
  *{box-sizing:border-box;margin:0;padding:0}
  html,body{width:738px;height:1200px;overflow:hidden;background:var(--canvas);font-family:"Roboto",sans-serif;color:var(--ink)}
  .page{position:absolute;left:184px;top:10px;width:370px;height:1180px;background:var(--content);display:flex;flex-direction:column}
  .site-header{height:72px;flex:none;background:var(--header);display:flex;align-items:center;justify-content:space-between;padding:0 16px;color:var(--light)}
  .brand{display:flex;align-items:center;gap:10px}
  .brand-mark{width:34px;height:34px;border-radius:50%;background:var(--brand)}
  .brand-name{font-size:26px;font-weight:900;color:var(--brand);line-height:1;letter-spacing:.5px}
  .brand-tag{font-size:10px;font-weight:500;letter-spacing:1.5px;margin-top:4px}
  .menu-btn{width:26px;height:20px;display:flex;flex-direction:column;justify-content:space-between}
  .menu-btn span{height:3px;background:var(--light)}
  .hero{height:208px;flex:none;position:relative;background:linear-gradient(180deg,#8fc6e4 0%,#cfe6f1 45%,#5f8f52 75%,#e9eef0 100%)}
  .hero-panel{position:absolute;left:24px;right:24px;top:84px;height:96px;background:#1c2a23;display:flex;flex-direction:column;align-items:center;justify-content:center;gap:10px;color:var(--light)}
  .hero-title{font-size:22px;font-weight:900;letter-spacing:.5px;text-transform:uppercase}
  .play-btn{background:var(--red);color:var(--light);font-size:13px;font-weight:700;padding:9px 22px;border-radius:20px;text-transform:uppercase}
  .section-head{height:56px;flex:none;display:flex;align-items:center;justify-content:space-between;padding:0 14px}
  .section-title{font-size:21px;font-weight:700}
  .plays{display:flex;align-items:center;gap:6px;font-size:11px;font-weight:500;color:var(--ink)}
  .banner{height:88px;flex:none}
  .banner-a{background:linear-gradient(90deg,#3c5a6c,#7a8f8a 50%,#3a4f5a)}
  .banner-b{background:linear-gradient(90deg,#e6a4c8,#9fd4e8 40%,#f1d3a8 70%,#e4b33c)}
  .game-list{margin:10px;border:2px solid var(--card-line);flex:none}
  .game-item{display:flex;gap:12px;padding:10px;align-items:flex-start}
  .game-item + .game-item{border-top:2px solid var(--card-line)}
  .thumb{width:144px;height:81px;flex:none}
  .t1{background:linear-gradient(135deg,#7fb24a,#2f5a2a)}
  .t2{background:linear-gradient(135deg,#2a66c9,#e23b2a)}
  .t3{background:linear-gradient(135deg,#f0a430,#3b7fd0)}
  .t4{background:linear-gradient(135deg,#dd2a25,#5b6a78)}
  .game-title{font-size:16px;font-weight:700;margin-bottom:4px}
  .game-desc{font-size:11px;line-height:1.35;color:var(--muted);margin-bottom:8px}
  .game-item .plays{font-size:10px}
  .bottom-bar{height:48px;flex:none;background:var(--red);display:flex;justify-content:center;margin-top:auto}
  .bottom-bar .menu-box{width:92px;background:var(--header);display:flex;align-items:center;justify-content:center}
  .site-footer{height:88px;flex:none;background:var(--header);display:flex;flex-direction:column;align-items:center;justify-content:center;gap:12px;font-size:12px;color:var(--light)}
  .site-footer a{color:var(--light);text-decoration:underline;font-size:13px}
</style>
</head>
<body>
<div class="page">
  <header class="site-header">
    <div class="brand">
      <div class="brand-mark"></div>
      <div>
        <div class="brand-name">Vultaroo</div>
        <div class="brand-tag">ONLINE GAMES</div>
      </div>
    </div>
    <div class="menu-btn"><span></span><span></span><span></span></div>
  </header>

  <section class="hero" role="img" aria-label="Snowy winter game scene with characters">
    <div class="hero-panel">
      <div class="hero-title">Winter Otter Dash</div>
      <div class="play-btn">Play now</div>
    </div>
  </section>

  <div class="section-head">
    <h2 class="section-title">At veroesamus</h2>
    <div class="plays">
      <svg width="16" height="10" viewBox="0 0 16 10"><rect width="16" height="10" rx="2" fill="#e3231b"/><polygon points="6,2 11,5 6,8" fill="#fff"/></svg>
      511 Plays
    </div>
  </div>

  <div class="banner banner-a" role="img" aria-label="Castle strategy game preview"></div>

  <div class="game-list">
    <div class="game-item">
      <div class="thumb t1" role="img" aria-label="Soldier action game preview"></div>
      <div>
        <div class="game-title">Lorem Ipsum</div>
        <div class="game-desc">Lorem ipsum dolor sit amet,<br>consectetur adipiscing elit,</div>
        <div class="plays"><svg width="14" height="9" viewBox="0 0 16 10"><rect width="16" height="10" rx="2" fill="#e3231b"/><polygon points="6,2 11,5 6,8" fill="#fff"/></svg>51,000,000 Plays</div>
      </div>
    </div>
    <div class="game-item">
      <div class="thumb t2" role="img" aria-label="Billiard balls game preview"></div>
      <div>
        <div class="game-title">Lorem Ipsum</div>
        <div class="game-desc">Lorem ipsum dolor sit amet,<br>consectetur adipiscing elit,</div>
        <div class="plays"><svg width="14" height="9" viewBox="0 0 16 10"><rect width="16" height="10" rx="2" fill="#e3231b"/><polygon points="6,2 11,5 6,8" fill="#fff"/></svg>51,000,000 Plays</div>
      </div>
    </div>
  </div>

  <div class="banner banner-b" role="img" aria-label="Dress-up and cooking game preview"></div>

  <div class="game-list">
    <div class="game-item">
      <div class="thumb t3" role="img" aria-label="Flying adventure game preview"></div>
      <div>
        <div class="game-title">Lorem Ipsum</div>
        <div class="game-desc">Lorem ipsum dolor sit amet,<br>consectetur adipiscing elit,</div>
        <div class="plays"><svg width="14" height="9" viewBox="0 0 16 10"><rect width="16" height="10" rx="2" fill="#e3231b"/><polygon points="6,2 11,5 6,8" fill="#fff"/></svg>51,000,000 Plays</div>
      </div>
    </div>
    <div class="game-item">
      <div class="thumb t4" role="img" aria-label="Red sports car racing game preview"></div>
      <div>
        <div class="game-title">Lorem Ipsum</div>
        <div class="game-desc">Lorem ipsum dolor sit amet,<br>consectetur adipiscing elit,</div>
        <div class="plays"><svg width="14" height="9" viewBox="0 0 16 10"><rect width="16" height="10" rx="2" fill="#e3231b"/><polygon points="6,2 11,5 6,8" fill="#fff"/></svg>51,000,000 Plays</div>
      </div>
    </div>
  </div>

  <div class="bottom-bar">
    <div class="menu-box"><div class="menu-btn"><span></span><span></span><span></span></div></div>
  </div>

  <footer class="site-footer">
    <div>© 2020 Vultaroo Ltd.All Rights Reserved</div>
    <a href="#">Affiliate Program</a>
  </footer>
</div>
</body>
</html>
```